Business card for law firm

Need business card for new law firm. Think confident, authoritative, conservative, but not stuffy or old-fashioned.

Contact Information for Business Card

Content for card - logo (uploaded), plus the following:

Paul Whitcombe (larger font)
Managing Partner (larger font, but not as large as name)
Level 9, 7 Ferris Lane
Sydney NSW 2000
Main Tel 02 9364 2710
Direct Tel 02 8472 3159
Email paul@qvlegal.com.au
www.qvlegal.com.au

Letterhead design should include logo plus:
Level 9, 7 Ferris Lane
Sydney NSW 2000
Tel 02 8472 3159
www.qvlegal.com.au

```html
<!DOCTYPE html>
<html lang="en">
<head>
<meta charset="utf-8">
<title>Quayvale Lawyers – Business Card</title>
<link rel="stylesheet" href="https://fonts.googleapis.com/css2?family=Open+Sans:wght@400;700&display=swap">
<style>
  :root {
    --bg: #e9e9eb;
    --card: #ffffff;
    --navy: #0f2468;
    --ink: #1c1c1c;
    --muted: #3a3a3a;
    --rule: #c9c9c9;
    --band-dark: #111111;
  }
  * { box-sizing: border-box; margin: 0; padding: 0; }
  html, body { width: 1200px; height: 900px; overflow: hidden; }
  body {
    background: var(--bg);
    font-family: "Open Sans", Arial, sans-serif;
    display: flex;
    align-items: center;
    justify-content: center;
    gap: 50px;
  }
  .card {
    position: relative;
    width: 540px;
    height: 330px;
    background: var(--card);
    border-radius: 18px;
    overflow: hidden;
    box-shadow: 0 6px 22px rgba(0,0,0,0.12);
  }
  .brand {
    display: flex;
    align-items: center;
    gap: 14px;
    color: var(--ink);
    font-weight: 700;
    letter-spacing: 0.16em;
    text-transform: uppercase;
    line-height: 1.25;
  }
  .brand-mark { background: var(--navy); flex: none; }

  /* contact side */
  .card-front .brand-zone {
    position: absolute;
    left: 0; top: 0;
    width: 262px; height: 318px;
    display: flex; align-items: center; justify-content: center;
  }
  .card-front .brand { font-size: 17px; }
  .card-front .brand-mark { width: 22px; height: 22px; }
  .divider {
    position: absolute;
    left: 262px; top: 60px;
    width: 1px; height: 160px;
    background: var(--rule);
  }
  .contact {
    position: absolute;
    left: 290px; top: 62px;
    color: var(--muted);
    font-size: 12.5px;
    line-height: 1.4;
  }
  .contact .name {
    color: var(--navy);
    font-weight: 700;
    font-size: 19px;
    text-transform: uppercase;
    line-height: 1.1;
  }
  .contact .role { font-size: 14px; margin-bottom: 10px; }
  .contact .address { margin-bottom: 10px; }
  .contact ul { list-style: none; }
  .contact li { display: flex; align-items: center; gap: 7px; }
  .contact svg { width: 11px; height: 11px; fill: var(--navy); flex: none; }
  .band {
    position: absolute; left: 0; bottom: 0;
    width: 100%; height: 12px;
    display: flex;
  }
  .band-navy { width: 62%; background: var(--navy); }
  .band-dark { flex: 1; background: var(--band-dark); }

  /* logo side */
  .card-back {
    display: flex; align-items: center; justify-content: center;
    background: #f7f7f7;
  }
  .card-back .brand { font-size: 28px; gap: 20px; }
  .card-back .brand-mark { width: 34px; height: 34px; }
</style>
</head>
<body>
  <article class="card card-front">
    <div class="brand-zone">
      <div class="brand"><span class="brand-mark"></span><span>Quayvale<br>Lawyers</span></div>
    </div>
    <div class="divider"></div>
    <div class="contact">
      <p class="name">Paul Whitcombe</p>
      <p class="role">Managing Partner</p>
      <p class="address">Level 9, 7 Ferris Lane<br>Sydney NSW 2000</p>
      <ul>
        <li><svg viewBox="0 0 24 24"><path d="M6.6 10.8a15.1 15.1 0 0 0 6.6 6.6l2.2-2.2c.3-.3.7-.4 1-.2 1.1.4 2.3.6 3.6.6.6 0 1 .4 1 1V20c0 .6-.4 1-1 1A17 17 0 0 1 3 4c0-.6.4-1 1-1h3.5c.6 0 1 .4 1 1 0 1.3.2 2.5.6 3.6.1.3 0 .7-.2 1z"/></svg>02 9364 2710 (Main)</li>
        <li><svg viewBox="0 0 24 24"><path d="M6.6 10.8a15.1 15.1 0 0 0 6.6 6.6l2.2-2.2c.3-.3.7-.4 1-.2 1.1.4 2.3.6 3.6.6.6 0 1 .4 1 1V20c0 .6-.4 1-1 1A17 17 0 0 1 3 4c0-.6.4-1 1-1h3.5c.6 0 1 .4 1 1 0 1.3.2 2.5.6 3.6.1.3 0 .7-.2 1z"/></svg>02 8472 3159 (Direct)</li>
        <li><svg viewBox="0 0 24 24"><path d="M2 5h20v14H2z M4 7v.5l8 5 8-5V7l-8 5z" fill-rule="evenodd"/></svg>paul@qvlegal.com.au</li>
        <li><svg viewBox="0 0 24 24"><circle cx="12" cy="12" r="10"/></svg>www.qvlegal.com.au</li>
      </ul>
    </div>
    <div class="band"><span class="band-navy"></span><span class="band-dark"></span></div>
  </article>

  <article class="card card-back">
    <div class="brand"><span class="brand-mark"></span><span>Quayvale<br>Lawyers</span></div>
  </article>
</body>
</html>
```